Oriva Soins: Symposium annuel 2018

You created the flyer "Atelier des ponts" for us at the beginning of the year. We would like to work in a new version. More details can be found in the briefing! Flyer (red, gray, black) - flyer wants to be white! - Flyer wants to be White! All further information can be found in the document in the appendix!

```html
<!DOCTYPE html>
<html lang="fr">
<head>
<meta charset="utf-8">
<title>Oriva Soins – Symposium annuel 2018</title>
<link href="https://fonts.googleapis.com/css2?family=Oswald:wght@400;500;600&family=Montserrat:wght@400;500;600&display=swap" rel="stylesheet">
<style>
  :root{
    --red:#e30613;
    --ink:#1a1a1a;
    --grey:#6f6f6f;
    --rule:#c9c9c9;
    --paper:#ffffff;
    --bg:#ffffff;
    --navy:#0f1e3d;
  }
  *{margin:0;padding:0;box-sizing:border-box}
  html,body{width:1200px;height:1200px;overflow:hidden;background:var(--bg)}
  body{position:relative;font-family:"Montserrat",sans-serif;color:var(--ink)}
  .page{position:absolute;top:233px;width:519px;height:734px;background:var(--paper);overflow:hidden}
  .front{left:48px;background:linear-gradient(#f4f4f4,#ececec)}
  .back{left:625px}
  .abs{position:absolute;left:0;right:0;text-align:center}
  .network{position:absolute;left:40px;top:0;width:440px;height:440px;border-radius:50%;
    background:radial-gradient(circle,rgba(255,255,255,1) 44%,rgba(180,180,180,.45) 58%,rgba(230,230,230,.2) 72%,rgba(240,240,240,0) 80%)}
  .cond{font-family:"Oswald",sans-serif;line-height:1}
  .title-red{top:110px;font-size:36px;font-weight:600;color:var(--red)}
  .title-black{top:148px;font-size:36px;font-weight:500;color:var(--ink)}
  .sym{top:205px;font-size:23px;color:var(--red)}
  .org{top:236px;font-size:22px}
  .date{top:278px;font-size:15px;color:var(--red)}
  .time{top:297px;font-size:15px}
  .venue{top:331px;font-size:14px;color:var(--red)}
  .society{top:457px;font-size:25px;font-weight:400}
  .dept{top:489px;font-size:25px;color:var(--red)}
  .form{position:absolute;left:24px;top:531px;width:472px;height:76px;background:rgba(255,255,255,.75);font-size:12px;padding:10px 4px}
  .form p{display:flex;margin-bottom:14px;white-space:nowrap}
  .form .dots{flex:1;border-bottom:1px dotted #555;margin:0 2px 3px}
  .bulletin{top:614px;font-size:12px;font-weight:600}
  .contact{top:640px;font-size:12px;font-weight:600}
  .contact span{font-weight:400}
  .brand{top:674px;display:flex;justify-content:center;align-items:center;gap:8px;font-size:21px;font-weight:600;color:var(--ink);letter-spacing:.5px}
  .brand i{width:16px;height:16px;background:var(--red);display:block}
  .header{position:absolute;left:24px;top:35px;width:469px;height:38px;background:var(--red);color:#fff;font-family:"Oswald",sans-serif;font-size:27px;line-height:38px;padding-left:7px;letter-spacing:-.5px;white-space:nowrap}
  .row{position:absolute;left:24px;width:469px;display:flex;align-items:center;transform:translateY(-50%)}
  .row .t{width:125px;padding-left:10px;font-size:16px;color:var(--red);font-weight:500}
  .row .d{flex:1;font-size:11.5px;line-height:1.3}
  .row .d b{font-weight:600}
  .rule{position:absolute;left:24px;width:469px;height:1px;background:var(--rule)}
  .thanks{position:absolute;left:24px;top:601px;width:469px;height:29px;background:var(--grey);border-radius:3px;color:#fff;font-size:12px;font-weight:500;text-align:center;line-height:29px}
  .sponsors-label{top:650px;font-size:12px;font-weight:500}
  .sponsors{position:absolute;left:24px;top:690px;width:469px;display:flex;justify-content:space-between;align-items:center;font-size:13px;font-weight:600}
  .sponsors span{color:var(--navy)}
</style>
</head>
<body>
  <section class="page front">
    <div class="network" role="img" aria-label="Réseau de points et de lignes grises formant un cercle décoratif"></div>
    <div class="abs cond title-red">ATELIER</div>
    <div class="abs cond title-black">DES PONTS</div>
    <div class="abs cond sym">SYMPOSIUM ANNUEL</div>
    <div class="abs cond org">ORIVA SOINS</div>
    <div class="abs cond date">27 SEPTEMBRE 2018</div>
    <div class="abs cond time">DE 14H00 À 18H00</div>
    <div class="abs cond venue">AUDITOIRE HÉLÈNE MARIN, CHRL</div>
    <div class="abs society">Société Alpine de Vasculologie</div>
    <div class="abs dept">Médicine interne Générale</div>
    <div class="form">
      <p>Nom<span class="dots"></span>Prénom<span class="dots"></span></p>
      <p>&nbsp;Timbre et signature :<span class="dots"></span></p>
    </div>
    <div class="abs bulletin">Bulletin d’inscription à retourner :</div>
    <div class="abs contact">par fax&nbsp; 021 555 01 23 ou e-mail : <span>info@orivasoins.ch</span></div>
    <div class="abs brand"><i></i>ORIVA SOINS</div>
  </section>

  <section class="page back">
    <div class="header">Actualisation des connaissances en lymphologie</div>

    <div class="row" style="top:101px"><div class="t">14:00-14:10</div><div class="d"><b>Bienvenue</b></div></div>
    <div class="rule" style="top:121px"></div>
    <div class="row" style="top:146px"><div class="t">14:10-14:40</div><div class="d"><b>A la découverte des lymphatiques : place de l’IRM</b><br>Pr A. Rinaldi, Università di Castelvero, Italy</div></div>
    <div class="rule" style="top:172px"></div>
    <div class="row" style="top:201px"><div class="t">14:45-15:15</div><div class="d"><b>Une entité nouvelle : le système « glymphatique »</b><br>M. L. Varin, Service d’Angiologie, CHRL, Lausanne</div></div>
    <div class="rule" style="top:225px"></div>
    <div class="row" style="top:257px"><div class="t">15:20 - 15:50</div><div class="d"><b>Approche psychosomatique du lymphœdème</b><br>Dr K. Albrecht, biologiste et psychologue, cabinet spécialisé en psycho-oncologie, Heidelberg, Allemagne</div></div>
    <div class="rule" style="top:296px"></div>
    <div class="row" style="top:320px"><div class="t">15:50 - 16:10</div><div class="d"><b>Pause</b></div></div>
    <div class="rule" style="top:344px"></div>
    <div class="row" style="top:378px"><div class="t">16:10 - 16:40</div><div class="d"><b>Prévenir le lymphœdème lors de la chirurgie oncologique: l’expérience FLUXA</b><br>Pr G. Ferrante, Université de Montaleto, Italie</div></div>
    <div class="rule" style="top:415px"></div>
    <div class="row" style="top:449px"><div class="t">16:45 - 17:15</div><div class="d"><b>Quand traiter le lymphœdème par voie chirurgicale ?</b><br>Dr R. Costa, Service de chirurgie plastique et reconstructive, CHRL, Lausanne</div></div>
    <div class="rule" style="top:493px"></div>
    <div class="row" style="top:523px"><div class="t">17:20 - 17:50</div><div class="d"><b>Le vaisseau lymphatique artificiel : mythe ou réalité ?</b><br>Pr C. Morel, Service d’Angiologie, CHRL, Lausanne</div></div>
    <div class="rule" style="top:554px"></div>
    <div class="row" style="top:576px"><div class="t">17 :55 - 18.00</div><div class="d"><b>Conclusion</b></div></div>

    <div class="thanks">Nous remercions chaleureusement nos sponsors pour leur soutien :</div>
    <div class="abs sponsors-label">SPONSORS</div>
    <div class="sponsors">
      <span>VELDA</span>
      <span>NORAMED</span>
      <span>santelis</span>
      <span>Keller &amp; Brandt</span>
      <span>TORVIK</span>
    </div>
  </section>
</body>
</html>
```